International Film making Business needs the 5 Logos provided made into a POSTER Format

Design Task:
CREATE A POSTER DESIGN USING THE 5 LOGOS PROVIDED. The BOLD BRIGHT HORIZON LOGO should stand out from the others by being in the middle with the other 4 logos connected to it somehow.

The 5 Businesses already has their 5 Logos, all similar in design to each other.

BOLD BRIGHT HORIZON is the Main Logo that encompasses the other 4 Logos. So it must stand out more and it is like the Overall Business entity that incorporates the other 4 Logos.

What is required is that by using the 5 Logo designs provided, create a cool graphic artwork that somehow incorporates ALL of the 5 Logos - But having the BOLD BRIGHT HORIZON Logo at the forefront/most important/standing out the most.
- BOLD BRIGHT HORIZON will probably be bigger than the others
- and could be changed into 3D.

I have attached all 5 logos and a hand drawn example of how the BOLD BRIGHT HORIZONS could stand out from the rest.

THE DESIGNS OF THE LOGOS SHOULD NOT BE CHANGED (except the BOLDBRIGHTHORIZON which can be 3D)

Please do not be restricted with the sample idea. Creativity is encouraged

DIMENSION: 3000 mm x 6000 mm
high resolution graphic

Logo Text

bold bright , bold bright pictures, bold bright legends, bold bright groovy, BOLD BRIGHT HORIZONS

Requirements
Must have
• USE THE 5 LOGOS PROVIDED ONLY - Only BOLD BRIGHT HORIZON can be changed into 3D only
Nice to have
• Eye catching design, showing the Bold Bright Horizon as the most powerful Logo that has the other 4 as subordinate companies
Should not have
• ANY CHANGE IN THE 5 LOGO DESIGNS (EXcept 3D for Bold Bright Horizons)

```html
<!DOCTYPE html>
<html lang="en">
<head>
<meta charset="utf-8">
<title>Bold Bright Horizons – Poster</title>
<link href="https://fonts.googleapis.com/css2?family=Montserrat:wght@400;600&display=swap" rel="stylesheet">
<style>
  :root {
    --gold-deep: #b8862e;
    --gold-light: #f4e3a6;
    --white: #ffffff;
    --ink: #3c3d40;
    --grey-text: #7b7d80;
    --mark: #8e9094;
    --blue-dark: #283a8e;
    --blue-light: #1aa7e0;
    --black: #0c0c0c;
    --grey-mid: #8a8b8d;
    --purple: #6a2c91;
    --green-dark: #0a703a;
    --green-light: #8cc63f;
  }
  html, body {
    margin: 0;
    padding: 0;
    width: 1200px;
    height: 600px;
    overflow: hidden;
    background: var(--white);
  }
  .poster {
    display: block;
    width: 1200px;
    height: 600px;
  }
  .brand-name {
    font-family: "Montserrat", "Helvetica", sans-serif;
    font-weight: 600;
    fill: var(--ink);
  }
  .brand-web {
    font-family: "Montserrat", "Helvetica", sans-serif;
    font-weight: 400;
    fill: var(--grey-text);
  }
  .brand-dot { fill: var(--mark); }
</style>
</head>
<body>
<svg class="poster" viewBox="0 0 2560 1288" preserveAspectRatio="none" xmlns="http://www.w3.org/2000/svg">
  <defs>
    <linearGradient id="gold-sheen" x1="0" y1="0" x2="1" y2="1">
      <stop offset="0" stop-color="var(--gold-deep)"/>
      <stop offset="0.3" stop-color="var(--gold-deep)"/>
      <stop offset="0.5" stop-color="var(--gold-light)"/>
      <stop offset="0.7" stop-color="var(--gold-deep)"/>
      <stop offset="1" stop-color="var(--gold-deep)"/>
    </linearGradient>
    <linearGradient id="sky-top" x1="0" y1="0" x2="1" y2="0">
      <stop offset="0" stop-color="var(--gold-deep)"/>
      <stop offset="0.15" stop-color="var(--gold-deep)"/>
      <stop offset="0.5" stop-color="var(--gold-light)"/>
      <stop offset="0.85" stop-color="var(--gold-deep)"/>
      <stop offset="1" stop-color="var(--gold-deep)"/>
    </linearGradient>
    <linearGradient id="band-blue" x1="0" y1="0" x2="1" y2="0">
      <stop offset="0" stop-color="var(--blue-dark)"/>
      <stop offset="0.6" stop-color="var(--blue-light)"/>
      <stop offset="1" stop-color="var(--blue-dark)"/>
    </linearGradient>
    <linearGradient id="band-black" x1="0" y1="0" x2="1" y2="0">
      <stop offset="0" stop-color="var(--black)"/>
      <stop offset="0.6" stop-color="var(--grey-mid)"/>
      <stop offset="1" stop-color="var(--black)"/>
    </linearGradient>
    <linearGradient id="band-rainbow" x1="0" y1="0" x2="1" y2="0">
      <stop offset="0" stop-color="var(--purple)"/>
      <stop offset="0.25" stop-color="#2a3b8f"/>
      <stop offset="0.45" stop-color="#1aa7e0"/>
      <stop offset="0.6" stop-color="#39b54a"/>
      <stop offset="0.78" stop-color="#fff200"/>
      <stop offset="1" stop-color="#ef4136"/>
    </linearGradient>
    <linearGradient id="band-green" x1="0" y1="0" x2="1" y2="0">
      <stop offset="0" stop-color="var(--green-dark)"/>
      <stop offset="0.5" stop-color="var(--green-light)"/>
      <stop offset="1" stop-color="var(--green-dark)"/>
    </linearGradient>
  </defs>

  <!-- backdrop -->
  <rect class="sky" x="267" y="0" width="2043" height="748" fill="url(#sky-top)"/>
  <rect class="band band-blue" x="267" y="748" width="523" height="540" fill="url(#band-blue)"/>
  <rect class="band band-black" x="790" y="748" width="495" height="540" fill="url(#band-black)"/>
  <rect class="band band-rainbow" x="1285" y="748" width="500" height="540" fill="url(#band-rainbow)"/>
  <rect class="band band-green" x="1785" y="748" width="525" height="540" fill="url(#band-green)"/>

  <!-- central peak -->
  <polygon class="peak-frame" points="1288,0 536,752 2040,752" fill="url(#gold-sheen)"/>
  <polygon class="peak-face" points="1288,40 576,752 2000,752" fill="var(--white)"/>
  <rect class="peak-base" x="543" y="748" width="1490" height="265" fill="var(--white)"/>

  <!-- sub-brand diamonds -->
  <g class="sub-diamond">
    <polygon points="543,745 811,1013 543,1281 275,1013" fill="url(#gold-sheen)"/>
    <polygon points="543,785 771,1013 543,1241 315,1013" fill="var(--white)"/>
  </g>
  <g class="sub-diamond">
    <polygon points="1040,745 1308,1013 1040,1281 772,1013" fill="url(#gold-sheen)"/>
    <polygon points="1040,785 1268,1013 1040,1241 812,1013" fill="var(--white)"/>
  </g>
  <g class="sub-diamond">
    <polygon points="1537,745 1805,1013 1537,1281 1269,1013" fill="url(#gold-sheen)"/>
    <polygon points="1537,785 1765,1013 1537,1241 1309,1013" fill="var(--white)"/>
  </g>
  <g class="sub-diamond">
    <polygon points="2033,745 2301,1013 2033,1281 1765,1013" fill="url(#gold-sheen)"/>
    <polygon points="2033,785 2261,1013 2033,1241 1805,1013" fill="var(--white)"/>
  </g>

  <!-- main brand -->
  <g class="brand-main">
    <circle class="brand-dot" cx="975" cy="580" r="125"/>
    <text class="brand-name" x="1165" y="590" font-size="76" textLength="560" lengthAdjust="spacing">BOLD BRIGHT</text>
    <text class="brand-name" x="1165" y="690" font-size="76" textLength="560" lengthAdjust="spacing">HORIZONS</text>
    <text class="brand-web" x="1165" y="740" font-size="38" textLength="560" lengthAdjust="spacing">boldbrighthorizons.com.au</text>
  </g>

  <!-- sub brands -->
  <g class="brand-sub">
    <circle class="brand-dot" cx="440" cy="1035" r="44"/>
    <text class="brand-name" x="500" y="1030" font-size="40">BOLD</text>
    <text class="brand-name" x="500" y="1080" font-size="40">BRIGHT</text>
  </g>
  <g class="brand-sub">
    <circle class="brand-dot" cx="915" cy="1035" r="40"/>
    <text class="brand-name" x="970" y="1030" font-size="30">BOLD BRIGHT</text>
    <text class="brand-name" x="970" y="1075" font-size="30">PICTURES</text>
  </g>
  <g class="brand-sub">
    <circle class="brand-dot" cx="1412" cy="1035" r="40"/>
    <text class="brand-name" x="1467" y="1030" font-size="30">BOLD BRIGHT</text>
    <text class="brand-name" x="1467" y="1075" font-size="30">LEGENDS</text>
  </g>
  <g class="brand-sub">
    <circle class="brand-dot" cx="2033" cy="960" r="45"/>
    <text class="brand-name" x="2033" y="1075" font-size="32" text-anchor="middle">BOLD BRIGHT</text>
    <text class="brand-name" x="2033" y="1122" font-size="32" text-anchor="middle">GROOVY</text>
  </g>
</svg>
</body>
</html>
```